Luxury Real Estate Website, Midwest, United States

We need web design services for a luxury website. We need IDX Integration with our MLS. We want this to be a very simple website with amazing graphics. We want it to link up with our MailChimp account in order to generate leads through a "More Information" Pop up on the main page. We want the main page to be covered with one large graphic that is a rolling slideshow of active listings of $400,000 and up from the IDX Integration. We need this website to give a very exclusive and sleek look. Lots of black is good... I will upload our logos in Black and Silver. We will also need an "About" page that we are going to call "Qeno Info". We want our graphics to be extremely impressive. Keep in mind, we are a company in the Midwest of the United States, and our real estate has a different look than homes in California or Florida. We need graphics that are realistic for the Midwest, yet still high-end.
Target Market(s)
Luxury Homeowners in the Midwest United States. The graphics needs to be pristine.
Industry/Entity Type
Real Estate
Coding
Coded - Design and coding required
Number of Pages Required
3 page
Requirements
Must have
- Large graphics with IDX Integration. The photos of real estate need to represent real estate that is common in the Midwest, United States. We also need MailChimp integration. We need a pop up that is titled "My Free Market Analysis" that makes them fill out a contact form asking for Full Name, Email Address, Phone Number and Address. This needs to be a pop up on the front page and will integrate with our MailChimp account. We also need a page called "About Qe No Home". And another page where clients can download informational PDFs. The main component needs to be a front page search engine connected with the IDX to access active listings from our MLS. I attached our logos and a sample front page of a website. I would love for ours to look similar.
Nice to have
- Lake House photos on midwest lakes are a plus.
Should not have
- Should not have clutter. This website needs to be clean, luxurious and exclusive.

```html
<!DOCTYPE html>
<html lang="en">
<head>
<meta charset="utf-8">
<title>Hearthstone Realty Group</title>
<link rel="stylesheet" href="https://fonts.googleapis.com/css2?family=Poppins:wght@400;500&family=Open+Sans:wght@400;600&display=swap">
<style>
:root{
  --black:#0d0d0d;
  --footer:#141414;
  --white:#ffffff;
  --ink:#222222;
  --muted:#555555;
  --footer-text:#dddddd;
  --accent:#c5d5e8;
  --navy:#1e3a55;
  --navy-dark:#15293d;
  --caption:#111111;
}
*{box-sizing:border-box;margin:0;padding:0}
html,body{width:1200px;height:3600px;overflow:hidden}
body{position:relative;background:var(--white);font-family:"Open Sans",Arial,sans-serif;color:var(--ink)}
.abs{position:absolute}
h1,h2,h3,.brand{font-family:"Poppins",Arial,sans-serif;font-weight:400}

.site-header{left:0;top:0;width:1200px;height:96px;background:var(--black);color:var(--white)}
.brand{position:absolute;left:91px;top:34px;font-size:20px;letter-spacing:.5px;color:var(--white);display:flex;align-items:center;gap:10px;white-space:nowrap}
.brand-mark{width:12px;height:12px;border:2px solid var(--white)}
.nav{position:absolute;top:41px;font-size:15px;color:var(--white);white-space:nowrap}
.nav-phone{font-size:20px;top:37px;display:flex;align-items:center;gap:8px}

.hero{left:0;top:96px;width:1200px;height:619px;background:linear-gradient(180deg,#5d7a52 0%,#3f5a3a 45%,#6b6456 75%,#4a5240 100%)}
.hero-title{left:0;top:312px;width:1200px;text-align:center;font-size:44px;color:var(--white);font-weight:500}
.search{left:221px;top:413px;width:758px;height:55px;background:var(--white);display:flex}
.search span{flex:1;padding-left:28px;line-height:55px;font-size:16px;color:var(--ink)}
.search-btn{width:70px;height:55px;background:var(--accent);display:flex;align-items:center;justify-content:center}

.about-card{left:89px;top:617px;width:1022px;height:319px;background:var(--white);box-shadow:0 4px 16px rgba(0,0,0,.25);display:flex}
.about-media{width:465px;height:319px;background:linear-gradient(180deg,#4f7fb8 0%,#2d4a70 55%,#6a3d3a 80%,#2a3346 100%)}
.about-body{padding:42px 46px 0 50px;flex:1}
.about-body h2{font-size:26px;margin-bottom:12px;white-space:nowrap}
.about-body p{font-size:13px;line-height:23px;color:var(--muted)}
.btn-pill{display:inline-block;margin-top:14px;padding:5px 22px;border-radius:20px;background:var(--accent);font-size:13px;color:var(--ink)}

.section-title{left:0;width:1200px;text-align:center;font-size:36px;color:var(--ink)}
.section-sub{left:0;width:1200px;text-align:center;font-size:15px;color:var(--muted)}
.service{width:300px;text-align:center}
.service svg{display:block;margin:0 auto}
.service h3{font-size:22px;margin-top:28px;font-weight:500}
.service p{font-size:14px;line-height:22px;color:var(--muted);margin-top:10px;padding:0 10px}
.service .chev{margin-top:8px;font-size:18px}

.projects{left:0;top:1567px;width:1200px;height:619px;background:linear-gradient(180deg,var(--navy) 0%,var(--navy-dark) 100%)}
.projects .section-title{color:var(--white);top:72px;text-transform:uppercase}
.project{width:322px;height:319px;top:178px}
.project-photo{height:261px}
.project-cap{height:58px;background:var(--caption);color:var(--white);font-size:20px;display:flex;align-items:center;justify-content:space-between;padding:0 22px}
.view-more{left:0;top:551px;width:1200px;text-align:center;color:var(--white);font-size:14px}

.testi{width:454px;height:226px;top:2400px;border:2px solid #e2e2e2;border-radius:6px;background:var(--white)}
.avatar{position:absolute;left:-30px;top:53px;width:120px;height:120px;border-radius:50%;background:linear-gradient(180deg,#b9a28a,#6e5a49);border:4px solid var(--white)}
.testi-body{position:absolute;left:110px;top:48px;width:300px}
.testi-body h3{font-size:18px;font-weight:400}
.testi-body p{font-size:14px;line-height:24px;color:#888;margin-top:10px;text-align:center}
.testi-name{text-align:right;font-size:17px;color:var(--navy);margin-top:6px}
.quote{position:absolute;right:30px;top:8px;font-family:"Poppins",Arial,sans-serif;font-size:90px;line-height:1;color:#bbb}
.arrow-side{top:2490px;font-size:40px;color:#444}

.footer{left:0;top:3074px;width:1200px;height:526px;background:var(--footer)}
.contact-box{left:134px;top:2875px;width:932px;height:387px;background:var(--white);border:1px solid #999;display:flex}
.contact-form{width:444px;padding:28px 55px}
.contact-form h3{font-size:22px;margin-bottom:22px;margin-left:-4px}
.field{height:44px;border:1px solid #bbb;margin-bottom:5px;font-size:13px;padding:10px 12px}
.field.tall{height:78px}
.map{flex:1;background:linear-gradient(135deg,#d9d9d9,#bdbdbd)}
.send{margin-top:16px;display:inline-block;padding:6px 28px;border-radius:20px;background:var(--accent);font-size:15px}

.f-head,.f-list,.f-contact,.f-mail,.copyright{color:var(--footer-text)}
.f-head{top:3322px;font-size:15px;color:var(--white)}
.f-list{top:3362px;font-size:13px;line-height:24px;list-style:none}
.f-list li::before{content:"» "}
.f-contact{top:3360px;left:432px;font-size:13px;line-height:20px}
.f-row{display:flex;gap:12px;margin-bottom:10px;align-items:flex-start}
.f-ico{width:20px;height:20px;border-radius:50%;background:#ddd;flex-shrink:0;display:flex;align-items:center;justify-content:center}
.f-mail{left:845px;top:3360px;width:240px;font-size:13px;line-height:20px}
.email-pill{margin-top:30px;width:216px;height:42px;border:1px solid #ddd;border-radius:22px;display:flex;align-items:center;justify-content:space-between;padding:0 14px 0 22px;font-size:13px}
.f-divider{left:89px;top:3518px;width:1022px;height:1px;background:#444}
.copyright{left:0;top:3554px;width:1200px;text-align:center;font-size:13px}
</style>
</head>
<body>

<header class="abs site-header">
  <div class="brand"><span class="brand-mark"></span>Hearthstone Realty</div>
  <span class="nav" style="left:365px">Home</span>
  <span class="nav" style="left:444px">Qeno Info</span>
  <span class="nav" style="left:547px">About Qe No Home</span>
  <span class="nav" style="left:720px">Downloads</span>
  <span class="nav" style="left:835px">Contact us</span>
  <span class="nav nav-phone" style="left:953px">
    <svg width="18" height="18" viewBox="0 0 24 24"><path fill="#fff" d="M6.6 10.8a15 15 0 0 0 6.6 6.6l2.2-2.2a1 1 0 0 1 1-.25 11.4 11.4 0 0 0 3.6.6 1 1 0 0 1 1 1V20a1 1 0 0 1-1 1A17 17 0 0 1 3 4a1 1 0 0 1 1-1h3.5a1 1 0 0 1 1 1c0 1.250.2 2.45.6 3.6a1 1 0 0 1-.25 1z"/></svg>
    (08) 5550 1274</span>
</header>

<section class="abs hero" role="img" aria-label="Lakeside home among tall pine trees"></section>
<h1 class="abs hero-title">Hearthstone Realty Group</h1>
<div class="abs search"><span>Search</span>
  <div class="search-btn"><svg width="22" height="22" viewBox="0 0 24 24"><circle cx="10" cy="10" r="6.5" fill="none" stroke="#1a2533" stroke-width="3"/><line x1="15" y1="15" x2="21" y2="21" stroke="#1a2533" stroke-width="3.2" stroke-linecap="round"/></svg></div>
</div>

<article class="abs about-card">
  <div class="about-media" role="img" aria-label="City skyline beside a river at dusk"></div>
  <div class="about-body">
    <h2>About&nbsp; Hearthstone Realty Group</h2>
    <p>It is a long established fact that a reader will be distracted by the readable content of a page when looking at its layout. The point of using Lorem Ipsum is that it has a more-or-less normal distribution of letters, as opposed to using 'Content here, content here', making it look like readable English. Many desktop publishing packages and web page editors now use Lorem Ipsum as their default model text,</p>
    <span class="btn-pill">Read More</span>
  </div>
</article>

<h2 class="abs section-title" style="top:1042px">Our Services</h2>
<p class="abs section-sub" style="top:1099px">It is a long established fact that a reader will be distracted by the readable content</p>

<div class="abs service" style="left:131px;top:1170px">
  <svg width="130" height="130" viewBox="0 0 130 130">
    <circle cx="56" cy="40" r="34" fill="var(--accent)"/>
    <g fill="none" stroke="#111" stroke-width="4" stroke-linejoin="round">
      <path d="M20 60 L55 32 L90 60"/><path d="M30 54 V108 H80 V54"/>
      <path d="M80 70 L100 58 L120 70 V108 H80"/>
      <rect x="45" y="84" width="18" height="24"/><rect x="40" y="62" width="12" height="12"/><rect x="58" y="62" width="12" height="12"/>
      <rect x="92" y="80" width="14" height="14"/>
    </g>
  </svg>
  <h3>Residential</h3>
  <p>The point of using Lorem Ipsum is that it has a more-or-less normal distribution of letters, as opposed</p>
  <div class="chev">&#8964;</div>
</div>

<div class="abs service" style="left:452px;top:1170px">
  <svg width="130" height="130" viewBox="0 0 130 130">
    <circle cx="65" cy="36" r="34" fill="var(--accent)"/>
    <g fill="none" stroke="#111" stroke-width="4">
      <circle cx="65" cy="65" r="30"/><circle cx="65" cy="65" r="12"/>
      <path d="M65 25v-8M65 105v8M25 65h-8M105 65h8M37 37l-6-6M93 93l6 6M93 37l6-6M37 93l-6 6"/>
      <rect x="22" y="100" width="86" height="12"/>
    </g>
  </svg>
  <h3>Qeno Info</h3>
  <p>The point of using Lorem Ipsum is that it has a more-or-less normal distribution of letters, as opposed</p>
  <div class="chev">&#8964;</div>
</div>

<div class="abs service" style="left:774px;top:1170px">
  <svg width="130" height="130" viewBox="0 0 130 130">
    <circle cx="60" cy="36" r="34" fill="var(--accent)"/>
    <g fill="none" stroke="#111" stroke-width="4">
      <rect x="30" y="30" width="36" height="80"/><rect x="66" y="50" width="34" height="60"/>
      <path d="M40 42h6M52 42h6M40 56h6M52 56h6M40 70h6M52 70h6M40 84h6M52 84h6M76 64h6M88 64h6M76 78h6M88 78h6M76 92h6M88 92h6"/>
      <path d="M20 110h90"/>
    </g>
  </svg>
  <h3>Commercial</h3>
  <p>The point of using Lorem Ipsum is that it has a more-or-less normal distribution of letters, as opposed</p>
  <div class="chev">&#8964;</div>
</div>

<section class="abs projects">
  <h2 class="abs section-title">Our Projects</h2>
  <div class="abs project" style="left:89px">
    <div class="project-photo" role="img" aria-label="White two-storey colonial house with lawn" style="background:linear-gradient(180deg,#6e93b8,#c9c9c4 55%,#4f7a3c)"></div>
    <div class="project-cap"><span>Porro quisquam quia</span><span>&#8594;</span></div>
  </div>
  <div class="abs project" style="left:439px">
    <div class="project-photo" role="img" aria-label="Brick family home with double garage" style="background:linear-gradient(180deg,#8fb3d4,#8a7560 55%,#5b7d3e)"></div>
    <div class="project-cap"><span>Porro quisquam quia</span><span>&#8594;</span></div>
  </div>
  <div class="abs project" style="left:790px">
    <div class="project-photo" role="img" aria-label="Grey sided house with red front door" style="background:linear-gradient(180deg,#7da6cc,#9aa0a6 55%,#4c7a38)"></div>
    <div class="project-cap"><span>Porro quisquam quia</span><span>&#8594;</span></div>
  </div>
  <div class="abs view-more">View More &raquo;</div>
</section>

<h2 class="abs section-title" style="top:2302px">TESTIMONIALS</h2>
<span class="abs arrow-side" style="left:50px">&#8249;</span>
<span class="abs arrow-side" style="left:1128px">&#8250;</span>

<div class="abs testi" style="left:130px">
  <div class="avatar" role="img" aria-label="Client portrait"></div>
  <span class="quote">&#8220;</span>
  <div class="testi-body">
    <h3>Neque porro quisquam</h3>
    <p>It is a long established fact that a reader will be distracted by the readable content of a page when looking at its layout.</p>
    <div class="testi-name">-&nbsp;&nbsp;Maren</div>
  </div>
</div>
<div class="abs testi" style="left:650px">
  <div class="avatar" role="img" aria-label="Client portrait"></div>
  <span class="quote">&#8220;</span>
  <div class="testi-body">
    <h3>Dolorem ipsum quia dolor</h3>
    <p>It is a long established fact that a reader will be distracted by the readable content of a page when looking at its layout.</p>
    <div class="testi-name">- Amet</div>
  </div>
</div>

<h2 class="abs section-title" style="top:2784px">CONTACT US</h2>

<footer class="abs footer"></footer>

<div class="abs contact-box">
  <form class="contact-form">
    <h3>Quick Contact</h3>
    <div class="field">Name</div>
    <div class="field">Phone number</div>
    <div class="field">Email address</div>
    <div class="field tall">Message</div>
    <span class="send">SEND</span>
  </form>
  <div class="map" role="img" aria-label="Street map of the office location"></div>
</div>

<div class="abs f-head" style="left:139px">INFORMATION</div>
<ul class="abs f-list" style="left:139px">
  <li>Privacy Policy</li><li>Qeno Info</li><li>About Qe No Home</li><li>Downloads</li>
</ul>

<div class="abs f-head" style="left:432px">CONTACT US</div>
<div class="abs f-contact">
  <div class="f-row"><span class="f-ico"><svg width="10" height="12" viewBox="0 0 10 12"><path fill="#141414" d="M5 0a4 4 0 0 1 4 4c0 3-4 8-4 8S1 7 1 4a4 4 0 0 1 4-4z"/></svg></span><span>Lakeview Business Centre<br>12 Harrow Rd, Lakeview Park, WA, 6099.</span></div>
  <div class="f-row"><span class="f-ico"><svg width="10" height="10" viewBox="0 0 24 24"><path fill="#141414" d="M6.6 10.8a15 15 0 0 0 6.6 6.6l2.2-2.2a1 1 0 0 1 1-.25 11 11 0 0 0 3.6.6 1 1 0 0 1 1 1V20a1 1 0 0 1-1 1A17 17 0 0 1 3 4a1 1 0 0 1 1-1h3.5a1 1 0 0 1 1 1c0 1.25.2 2.45.6 3.6a1 1 0 0 1-.25 1z"/></svg></span><span>(08) 5550 1274</span></div>
  <div class="f-row"><span class="f-ico"><svg width="11" height="8" viewBox="0 0 11 8"><rect x=".5" y=".5" width="10" height="7" fill="none" stroke="#141414"/><path d="M.5.5l5 4 5-4" fill="none" stroke="#141414"/></svg></span><span>hello@samplemail.com</span></div>
</div>

<div class="abs f-head" style="left:845px">JOIN OUR MAILING LIST</div>
<div class="abs f-mail">
  <p>Your about us information would fit here nicely.</p>
  <div class="email-pill"><span>Email address</span>
    <svg width="16" height="16" viewBox="0 0 16 16"><circle cx="8" cy="8" r="8" fill="#ddd"/><path d="M5 5l6 6M11 5l-6 6" stroke="#141414" stroke-width="1.6"/></svg>
  </div>
</div>

<div class="abs f-divider"></div>
<div class="abs copyright">Copyright &copy; 2018. All Rights Reserved</div>

</body>
</html>
```